Recruitment of Trellan Staffing for the UK market

I want a website for the UK market to attract businesses and companies to come to us for Philipine labour. We want an information site that gives all information on what we do and how we can recruit Philippine labour.
This is a recruitment site for companies to contact us with their requirements for skilled workers coming from the Philipines over to the UK to work.

Target Market(s)

Uk Companies and businesses who want Philipine skilled workers

Industry/Entity Type

REcruitment

Coding

Number of Pages Required

5+ page

Font styles to use
Sans Serif

Colors
0054AA
0677BA
7BADD7
CADEEF
E8F1F8
0094D4
00A9DD
6FCCEA
C7EBF8
E9F6FB
EE7325
F08F49
F5BC92
FAE3D3
FDF4ED
EB3D1F
EC4F4E
F09395
F8D3D4
FCEDEE

Requirements
Must have
• Look professional and corperate with drop down menus for Home ,about, services,articles. training , contact us
Nice to have
• Look at Velmora recruitment- https://velmorarecruitment.example.co.uk/. This is my current site - https://www.trellanstaffing.example.com/
Should not have
• Cartoons or silly pictures , needs to be corperate looking

```html
<!DOCTYPE html>
<html lang="en">
<head>
<meta charset="utf-8">
<title>Trellan Staffing – Skilled Philippine Workers for UK Companies</title>
<link rel="stylesheet" href="https://fonts.googleapis.com/css2?family=Lexend:wght@400;500;600&family=Roboto:wght@400;500&display=swap">
<style>
:root{
  --brand-red:#8e2e29;
  --brand-blue:#0677BA;
  --ink:#2b2b2b;
  --muted:#555;
  --soft-grey:#f2f2f2;
  --rule:#cfcfcf;
  --white:#fff;
  --contact-bg:#e3e9ef;
}
*{box-sizing:border-box;margin:0;padding:0}
html,body{width:1200px;height:4011px;overflow:hidden}
body{position:relative;font-family:"Roboto",sans-serif;color:var(--ink);background:var(--white)}
.abs{position:absolute}
.heading{font-family:"Lexend",sans-serif;font-weight:500}
.btn{position:absolute;display:flex;align-items:center;justify-content:center;background:var(--brand-red);color:var(--white);font-family:"Roboto",sans-serif;font-weight:500;font-size:14px;border-radius:3px;letter-spacing:.2px}
.btn-outline{position:absolute;width:108px;height:36px;border:2px solid var(--brand-red);border-radius:4px;color:var(--brand-red);font-size:11px;font-weight:500;display:flex;align-items:center;justify-content:center}

/* header */
.site-header{left:0;top:0;width:1200px;height:94px;background:var(--white)}
.brand-name{font-family:"Lexend",sans-serif;font-weight:600;color:var(--brand-red);font-size:26px;display:flex;align-items:center;gap:10px}
.brand-mark{width:14px;height:14px;background:var(--brand-red)}
.main-nav{left:436px;top:36px;display:flex;gap:33px;font-size:15px;color:#444}

/* hero */
.hero-photo{left:0;top:94px;width:1200px;height:556px;background:linear-gradient(120deg,#c9ccd2 0%,#8d97a3 40%,#3b4452 75%,#1f2632 100%)}
.hero-panel{left:112px;top:314px;width:464px;height:336px;background:rgba(17,108,186,.78)}
.hero-title{left:137px;top:372px;width:430px;color:var(--white);font-size:34px;line-height:53px}

/* about */
.about-ring{left:114px;top:734px;width:414px;height:414px;border-radius:50%;background:var(--brand-red)}
.about-photo{left:134px;top:738px;width:392px;height:392px;border-radius:50%;background:linear-gradient(160deg,#c3cbd6,#e9a165 60%,#5d6470)}
.about-title{left:599px;top:726px;font-size:31px;color:var(--ink)}
.about-title span,.contact-title span{color:var(--brand-blue)}
.about-text{left:599px;top:803px;width:489px;font-size:14.5px;line-height:26px;color:var(--muted);text-align:justify}
.thumb{top:963px;width:117px;height:104px}

/* working together */
.working{left:0;top:1234px;width:1200px;height:1234px;background:var(--soft-grey)}
.eyebrow{left:114px;top:1338px;font-size:15px;font-weight:500;color:var(--brand-blue)}
.working-title{left:110px;top:1380px;width:460px;font-size:33px;line-height:47px;color:var(--ink)}
.map{left:112px;top:1656px;width:467px;height:706px;background:linear-gradient(180deg,#8aadf3,#86a9f1)}
.service-rule{left:646px;width:442px;height:2px;background:var(--rule)}
.service-name{left:646px;font-size:25px;line-height:40px;color:var(--ink)}
.service-text{left:844px;width:244px;font-size:12.5px;line-height:21.3px;color:#333}

/* cards */
.card{top:2553px;width:434px;height:416px;border-radius:18px;overflow:hidden;background:var(--white);box-shadow:0 4px 14px rgba(0,0,0,.12)}
.card-photo{width:100%;height:341px}
.card-label{height:75px;display:flex;align-items:center;justify-content:center;font-family:"Lexend",sans-serif;font-weight:500;font-size:25px;color:var(--ink)}
.card.is-active .card-label{background:var(--brand-blue);color:var(--white)}

/* contact */
.contact{left:0;top:3054px;width:1200px;height:609px;background:linear-gradient(160deg,#e7ecf1,#d9e2ea 60%,#e4eaf0)}
.contact-title{left:0;top:3120px;width:1200px;text-align:center;font-size:31px;color:var(--ink)}
.field{background:var(--white);border-radius:5px;font-size:13.5px;color:#666;padding:0 22px;display:flex;align-items:center;box-shadow:0 1px 3px rgba(0,0,0,.05)}
.field.message{align-items:flex-start;padding-top:22px}

/* footer */
.foot-head{font-family:"Lexend",sans-serif;font-weight:600;font-size:23px;color:var(--ink)}
.copyright{left:110px;top:3860px;font-size:14.5px;line-height:27px;color:#777}
.foot-icon{width:36px;height:36px;border-radius:50%;background:var(--brand-blue)}
.foot-line{left:560px;font-size:15px;line-height:23px;color:#333}
.foot-line b{font-weight:500;color:var(--ink)}
.social{top:3803px;width:37px;height:37px;border:2px solid var(--brand-red);border-radius:50%}
</style>
</head>
<body>

<header class="abs site-header">
  <div class="abs brand-name" style="left:112px;top:30px"><span class="brand-mark"></span>Trellan Staffing</div>
  <nav class="abs main-nav"><span>Home</span><span>About</span><span>Services</span><span>Articles</span><span>Training</span><span>Contact Us</span></nav>
  <div class="btn" style="left:979px;top:26px;width:108px;height:41px">LOG IN</div>
</header>

<section>
  <div class="abs hero-photo" role="img" aria-label="Photo of smiling office professionals in a business meeting"></div>
  <div class="abs hero-panel"></div>
  <h1 class="abs heading hero-title">Recruiting and placing skilled Philippine workers into UK companies</h1>
  <div class="btn" style="left:137px;top:562px;width:135px;height:37px">GET STARTED</div>
</section>

<section>
  <div class="abs about-ring"></div>
  <div class="abs about-photo" role="img" aria-label="Photo of a smiling engineer in a hard hat and safety vest holding a tablet"></div>
  <h2 class="abs heading about-title">What the <span>business is about</span></h2>
  <p class="abs about-text">We source skilled workers directly from the Philippines to work in the UK. With offices , training locations and specialist recruiters we can find the highest quality individuals to add value and resources to any UK buisness. We delivery quality based on vast experience over a number of years.</p>
  <div class="abs thumb" style="left:599px;background:linear-gradient(#c9d8e8,#e2d5cc)" role="img" aria-label="Photo of healthcare staff"></div>
  <div class="abs thumb" style="left:726px;background:linear-gradient(#6fa0d2,#3f78b5)" role="img" aria-label="Photo of a team of workers in uniform"></div>
  <div class="abs thumb" style="left:853px;background:linear-gradient(#7fa8d0,#b85a4c)" role="img" aria-label="Photo of construction workers in hard hats"></div>
  <div class="abs thumb" style="left:980px;background:linear-gradient(#8d99a8,#c55348)" role="img" aria-label="Photo of technicians at work"></div>
  <div class="btn" style="left:599px;top:1100px;width:134px;height:42px">LEARN MORE</div>
</section>

<section class="abs working"></section>
<div class="abs eyebrow">WORKING TOGETHER</div>
<h2 class="abs heading working-title">We recruit the finest talent available with our dedicated 200 strong team. Our centres are highlighted in red dots on the map.</h2>
<div class="abs map" role="img" aria-label="Map of the Philippines with recruitment centres marked"></div>

<div class="abs service-rule" style="top:1341px"></div>
<h3 class="abs heading service-name" style="top:1420px">What we do</h3>
<div class="btn-outline" style="left:645px;top:1484px">LEARN MORE</div>
<p class="abs service-text" style="top:1388px">Our company has been estabilished in the Philippines for over 20 years. We have mainly been recruiting philippine workers for the off shore industry in asia but since brexit and the new rules on skilled workers entering the UK we have been working with UK companies who now have</p>

<div class="abs service-rule" style="top:1606px"></div>
<h3 class="abs heading service-name" style="top:1685px">How we help</h3>
<div class="btn-outline" style="left:645px;top:1749px">LEARN MORE</div>
<p class="abs service-text" style="top:1653px">We work with companies to find skilled workers that meet the UK requirements for Visas and work permits. We guide you through the whole process and deliver highly trained people that add value to your business. We are here to help both the companies and the Philippino people to gain a better standard of living for their</p>

<div class="abs service-rule" style="top:1863px"></div>
<h3 class="abs heading service-name" style="top:1941px">Where to start</h3>
<div class="btn-outline" style="left:645px;top:2005px">LEARN MORE</div>
<p class="abs service-text" style="top:1909px">We need to know what your issues are and how we can understand the personnal you require , over what time frame and the number of employees you need. Once this is estabilished we start sourcing workers in the Philippines that meet your criteria while starting the process in the UK to be able to have all</p>

<div class="abs service-rule" style="top:2127px"></div>
<h3 class="abs heading service-name" style="top:2185px;width:180px">Contact us today</h3>
<div class="btn-outline" style="left:645px;top:2290px">LEARN MORE</div>
<p class="abs service-text" style="top:2174px">We work with companies to find skilled workers that meet the UK requirements for Visas and work permits. We guide you through the whole process and deliver highly trained people that add value to your business. We are here to help both the companies and the Philippino people to gain a better standard of living for their</p>

<section>
  <div class="abs card" style="left:112px">
    <div class="card-photo" style="background:linear-gradient(170deg,#d9dde2,#b88a5c 55%,#6b6a63)" role="img" aria-label="Photo of a construction worker in a hard hat using a tablet"></div>
    <div class="card-label">UK Skilled Workers List</div>
  </div>
  <div class="abs card is-active" style="left:580px">
    <div class="card-photo" style="background:radial-gradient(circle at 50% 45%,#56606b,#262d35 70%)" role="img" aria-label="Photo of a hand pressing an approval stamp"></div>
    <div class="card-label">Sponsor Licence</div>
  </div>
  <div class="abs card" style="left:1050px">
    <div class="card-photo" style="background:linear-gradient(160deg,#2a2f36,#b58a6c 60%,#d8d3cd)" role="img" aria-label="Photo of hands reviewing candidate profiles"></div>
    <div class="card-label">Recruitment</div>
  </div>
</section>

<section class="abs contact"></section>
<h2 class="abs heading contact-title">Contact <span>Us</span></h2>
<div class="abs field" style="left:204px;top:3207px;width:384px;height:62px">First name</div>
<div class="abs field" style="left:611px;top:3207px;width:385px;height:62px">Last name</div>
<div class="abs field" style="left:204px;top:3300px;width:384px;height:62px">Email:</div>
<div class="abs field" style="left:611px;top:3300px;width:385px;height:62px">Phone</div>
<div class="abs field message" style="left:204px;top:3394px;width:792px;height:113px">Message:</div>
<div class="btn" style="left:541px;top:3545px;width:117px;height:42px">SUBMIT</div>

<footer>
  <div class="abs brand-name" style="left:112px;top:3765px;font-size:28px"><span class="brand-mark"></span>Trellan Staffing</div>
  <p class="abs copyright">©Copyrights 2023 Trellanstaffing &nbsp;|<br>All Rights Reserved</p>

  <h4 class="abs foot-head" style="left:507px;top:3745px">Contact</h4>
  <div class="abs foot-icon" style="left:509px;top:3808px">
    <svg width="36" height="36" viewBox="0 0 36 36"><path d="M18 10a5 5 0 0 0-5 5c0 4 5 10 5 10s5-6 5-10a5 5 0 0 0-5-5z" fill="#fff"/><circle cx="18" cy="15" r="1.8" fill="#0677BA"/></svg>
  </div>
  <p class="abs foot-line" style="top:3807px">Larkspur Gardens, Brimsworth<br>BR4 2 United Kingdom</p>
  <div class="abs foot-icon" style="left:509px;top:3876px">
    <svg width="36" height="36" viewBox="0 0 36 36"><path d="M13 11l3 0 1.5 4-2 1.5a9 9 0 0 0 4 4l1.5-2 4 1.5 0 3a2 2 0 0 1-2 2A13 13 0 0 1 11 13a2 2 0 0 1 2-2z" fill="#fff"/></svg>
  </div>
  <p class="abs foot-line" style="top:3873px"><b>Call Us</b><br>07700900417</p>
  <div class="abs foot-icon" style="left:509px;top:3939px">
    <svg width="36" height="36" viewBox="0 0 36 36"><rect x="11" y="13" width="14" height="10" rx="1" fill="#fff"/><path d="M11 14l7 5 7-5" stroke="#0677BA" stroke-width="1.4" fill="none"/></svg>
  </div>
  <p class="abs foot-line" style="top:3936px"><b>E mail Us</b><br>sales@trellanstaffing.example.com</p>

  <h4 class="abs foot-head" style="left:878px;top:3745px">Follow us</h4>
  <div class="abs social" style="left:878px" role="img" aria-label="Social profile link"></div>
  <div class="abs social" style="left:928px" role="img" aria-label="Social profile link"></div>
  <div class="abs social" style="left:978px" role="img" aria-label="Social profile link"></div>
  <div class="abs social" style="left:1028px" role="img" aria-label="Social profile link"></div>
</footer>

</body>
</html>
```